KVOR Individual and Corporate Development Business Card Design

KVOR needs a business card design that is aligned with it's values and targetted markets. Coherent Lattice of Adaptive Reasoning Method's self diagnosis model and tools, which can be used for personal improvement and team/business performance enhancement, is based on the learnings of over 20 years of medical practitioning. KVOR supercharges personal effectiveness and awareness to also increase team and business performance.

The targetted markets are high performance individuals and teams who aspire seek to enhance their capabilities and achieve their absolute best potential.

Look and feel for the business card design we are looking for is high technology, premium, fresh, new and medical.

Target Market(s)

Industry/Entity Type

Business Consultant

Contact Information for Business Card

Logo, Full Name, Title, Phone number, Email, company name, Address,

Font styles to use
Sans Serif

Requirements
Must have
• Tag line: Amplifying Capability for Truly Driven Minds
• Please use same colours as the logo.

```html
<!DOCTYPE html>
<html lang="en">
<head>
<meta charset="utf-8">
<title>KVOR Business Card</title>
<link rel="stylesheet" href="https://fonts.googleapis.com/css2?family=Arimo:wght@700&family=PT+Sans:wght@400;700&display=swap">
<style>
  :root {
    --page-bg: #e9e6e2;
    --card-black: #0d0d0d;
    --card-black-soft: #1a1a1a;
    --brand-teal: #1ba7c4;
    --text-light: #e8e8e8;
    --rule-grey: #6a6a6a;
  }
  * { margin: 0; padding: 0; box-sizing: border-box; }
  html, body {
    width: 1200px; height: 900px; overflow: hidden;
    background: var(--page-bg);
  }
  .canvas { position: relative; width: 1200px; height: 900px; }
  .card {
    position: absolute; left: 300px;
    width: 600px; height: 343px;
    background: linear-gradient(160deg, var(--card-black-soft), var(--card-black) 60%);
    box-shadow: 0 10px 28px rgba(0,0,0,0.25);
    overflow: hidden;
  }
  .card--front { top: 90px; }
  .card--back { top: 467px; }

  .tagline {
    position: absolute; left: 0; right: 0; top: 62px;
    text-align: center;
    font-family: "Arimo", Arial, sans-serif; font-weight: 700;
    font-size: 37px; line-height: 42px; letter-spacing: 3px;
    color: var(--brand-teal); text-transform: uppercase;
  }

  .brand {
    position: absolute; right: 44px; top: 40px;
    display: flex; flex-direction: column; align-items: flex-end;
  }
  .brand__name {
    font-family: "PT Sans", sans-serif; font-weight: 700;
    font-size: 62px; line-height: 62px; letter-spacing: 4px;
    color: var(--brand-teal);
  }
  .brand__full {
    margin-top: 6px;
    font-family: "PT Sans", sans-serif; font-weight: 700;
    font-size: 13px; line-height: 15px; text-transform: uppercase;
    text-align: right; color: var(--brand-teal); letter-spacing: 0.5px;
  }
  .brand-rule {
    position: absolute; right: 44px; top: 152px;
    width: 270px; height: 1px; background: var(--rule-grey);
  }

  .person {
    position: absolute; left: 40px; top: 212px;
    font-family: "PT Sans", sans-serif;
  }
  .person__name {
    font-size: 19px; line-height: 22px; color: var(--brand-teal);
    text-transform: uppercase; letter-spacing: 0.5px;
  }
  .person__title { font-size: 15px; line-height: 18px; color: var(--text-light); }
  .person-rule {
    position: absolute; left: 232px; top: 226px;
    width: 150px; height: 1px; background: var(--rule-grey);
  }

  .address {
    position: absolute; right: 44px; top: 206px;
    font-family: "PT Sans", sans-serif; font-size: 13px; line-height: 18px;
    color: var(--text-light); text-align: right;
  }

  .contacts {
    position: absolute; left: 40px; top: 266px; list-style: none;
    font-family: "PT Sans", sans-serif; font-size: 15px; line-height: 20px;
    color: var(--text-light);
  }
  .contacts li { display: flex; align-items: center; gap: 7px; }
  .contacts svg { width: 12px; height: 12px; fill: var(--brand-teal); flex: none; }
</style>
</head>
<body>
<main class="canvas">
  <section class="card card--front" aria-label="Card front">
    <p class="tagline">Amplifying<br>Capability<br>for Truly<br>Driven<br>Minds</p>
  </section>

  <section class="card card--back" aria-label="Card back">
    <div class="brand">
      <span class="brand__name">KVOR</span>
      <span class="brand__full">Coherent Lattice of<br>Adaptive Reasoning Method</span>
    </div>
    <div class="brand-rule"></div>

    <div class="person">
      <p class="person__name">Daniel Hartley</p>
      <p class="person__title">Managing Director</p>
    </div>
    <div class="person-rule"></div>

    <p class="address">5678, Lattice Row,<br>Countryland, 54321</p>

    <ul class="contacts">
      <li>
        <svg viewBox="0 0 24 24" aria-hidden="true"><path d="M6.6 10.8a15.1 15.1 0 0 0 6.6 6.6l2.2-2.2a1 1 0 0 1 1-.25 11.4 11.4 0 0 0 3.6.57 1 1 0 0 1 1 1V20a1 1 0 0 1-1 1A17 17 0 0 1 3 4a1 1 0 0 1 1-1h3.5a1 1 0 0 1 1 1c0 1.25.2 2.45.57 3.57a1 1 0 0 1-.25 1z"/></svg>
        (044)987654321
      </li>
      <li>
        <svg viewBox="0 0 24 24" aria-hidden="true"><path d="M2 5h20v14H2zM4 7v10h16V7l-8 6z"/></svg>
        hello@kvormail.com
      </li>
      <li>
        <svg viewBox="0 0 24 24" aria-hidden="true"><circle cx="12" cy="12" r="10"/></svg>
        www.kvorsite.com
      </li>
    </ul>
  </section>
</main>
</body>
</html>
```